Consulting company business cards

We have a base design, but would be willing to update. We have a new logo/"tag" that needs to be added. Current business card design is attached for reference into our "style."

Industry/Entity Type

Business

Contact Information for Business Card

Should contain name and title, office number, mobile number if appropriate, e-mail, website, physical address, and company logo.

Font styles to use
Other font styles liked:
• See current card design on KorvandBCard

Colors
0455a3
85acd3
aaaaaa

Requirements
Must have
• Our colors are navy blue, gray, and a lighter blue
Nice to have
• Design that I can easily drop in new names/titles as we hire employees.

```html
<!DOCTYPE html>
<html lang="en">
<head>
<meta charset="utf-8">
<title>Tarvell Business Cards</title>
<link rel="stylesheet" href="https://fonts.googleapis.com/css2?family=Lato:wght@400;700;900&family=Open+Sans:wght@400;600&display=swap">
<style>
  :root {
    --navy: #0b3a5e;
    --navy-deep: #082d4a;
    --sky: #85acd3;
    --gray: #8a8a8a;
    --paper: #f4f5f6;
    --stage: #1e1f21;
    --ink-light: #e9eef3;
  }
  * { margin: 0; padding: 0; box-sizing: border-box; }
  html, body {
    width: 1200px; height: 873px; overflow: hidden;
    background: var(--stage);
    font-family: "Lato", sans-serif;
  }
  .sheet {
    position: relative; width: 1200px; height: 873px;
    display: flex; align-items: center; justify-content: center; gap: 60px;
  }
  .card {
    position: relative; width: 520px; height: 300px;
    border-radius: 14px; overflow: hidden;
    box-shadow: 0 18px 40px rgba(0,0,0,.55);
  }

  /* Back: contact side */
  .card--contact { background: var(--navy); color: var(--ink-light); }
  .contact__strip {
    position: absolute; top: 0; right: 0; width: 128px; height: 100%;
    background: var(--paper);
    border-left: 4px solid var(--paper);
  }
  .contact__strip::before, .contact__strip::after {
    content: ""; position: absolute; top: 0; bottom: 0; width: 3px; background: var(--navy);
  }
  .contact__strip::before { left: 4px; }
  .contact__strip::after { left: 12px; }
  .contact__brand {
    position: absolute; top: 50%; left: 64px;
    transform: translate(-50%, -50%) rotate(90deg);
    display: flex; flex-direction: column; align-items: center; white-space: nowrap;
  }
  .contact__brand .brand-row { display: flex; align-items: center; gap: 10px; }
  .contact__brand .brand-name { font-size: 46px; }
  .contact__brand .brand-mark { width: 30px; height: 30px; }
  .contact__brand .brand-tagline { font-size: 10px; letter-spacing: 2px; }

  .contact__body { position: absolute; left: 40px; top: 34px; width: 330px; }
  .person__name { font-size: 17px; font-weight: 400; color: var(--sky); }
  .person__name b { font-weight: 700; color: var(--ink-light); }
  .person__title { font-size: 10px; font-weight: 700; margin-top: 2px; }
  .contact__address { font-size: 13px; font-weight: 700; margin-top: 58px; }
  .contact__list { list-style: none; margin-top: 44px; font-size: 13px; font-weight: 700; }
  .contact__list li { display: flex; align-items: center; gap: 10px; line-height: 20px; }
  .contact__list svg { width: 14px; height: 14px; fill: var(--ink-light); }

  /* Front: brand side */
  .card--brand { background: var(--paper); }
  .brand__strip {
    position: absolute; top: 0; right: 0; width: 78px; height: 100%;
    background: var(--navy);
  }
  .brand__rule {
    position: absolute; top: 0; bottom: 0; width: 3px; background: var(--navy);
  }
  .brand__rule--outer { right: 96px; }
  .brand__rule--inner { right: 86px; }
  .brand__web {
    position: absolute; top: 50%; right: 39px;
    transform: translate(50%, -50%) rotate(90deg);
    color: var(--ink-light); font-family: "Open Sans", sans-serif;
    font-size: 17px; letter-spacing: 2px; white-space: nowrap;
  }
  .brand__lockup { position: absolute; left: 40px; top: 96px; }
  .brand__lockup .brand-row { display: flex; align-items: center; gap: 16px; }
  .brand__lockup .brand-name { font-size: 74px; line-height: 1; }
  .brand__lockup .brand-mark { width: 66px; height: 66px; }
  .brand__lockup .brand-tagline { font-size: 15px; letter-spacing: 3px; margin-top: 6px; }

  .brand-name { font-family: "Lato", sans-serif; font-weight: 900; color: var(--navy); letter-spacing: 1px; }
  .brand-mark { border-radius: 50%; background: var(--sky); flex: none; }
  .brand-tagline { font-family: "Open Sans", sans-serif; color: var(--gray); text-transform: uppercase; }
</style>
</head>
<body>
<main class="sheet">
  <section class="card card--contact" aria-label="Business card, contact side">
    <div class="contact__body">
      <p class="person__name">Hollis <b>Korvand</b></p>
      <p class="person__title">Office Manager</p>
      <p class="contact__address">1180 W 54th St Brookdale Ohio 43210</p>
      <ul class="contact__list">
        <li><svg viewBox="0 0 16 16" aria-hidden="true"><path d="M2 6c0-3 3-4 6-4s6 1 6 4l-3 1-1-2H6L5 7 2 6zm2 2h8l2 6H2l2-6zm4 1.5a2 2 0 1 0 0 4 2 2 0 0 0 0-4z"/></svg>555.214.3380</li>
        <li><svg viewBox="0 0 16 16" aria-hidden="true"><path d="M4 1h8v4H4zM1 6h14v6h-3v3H4v-3H1zm4 4v4h6v-4z"/></svg>555.214.3391</li>
        <li><svg viewBox="0 0 16 16" aria-hidden="true"><path d="M1 3h14v10H1zm1.5 1.5L8 9l5.5-4.5v-.5h-11z"/></svg>Hkorvand@Tarvelltech.com</li>
      </ul>
    </div>
    <div class="contact__strip">
      <div class="contact__brand">
        <div class="brand-row"><span class="brand-name">TARVELL</span><span class="brand-mark"></span></div>
        <span class="brand-tagline">A Cloud Consulting Company</span>
      </div>
    </div>
  </section>

  <section class="card card--brand" aria-label="Business card, brand side">
    <div class="brand__lockup">
      <div class="brand-row"><span class="brand-name">TARVELL</span><span class="brand-mark"></span></div>
      <p class="brand-tagline">A Cloud Consulting Company</p>
    </div>
    <span class="brand__rule brand__rule--outer"></span>
    <span class="brand__rule brand__rule--inner"></span>
    <div class="brand__strip"><span class="brand__web">www.Tarvelltech.com</span></div>
  </section>
</main>
</body>
</html>
```